Call Center In Need of Website Design

We are a call center that provides inbound and outbound calling & marketing services for eCommerce store. We would like to see a fun, creative, playful design that is simple.

Here are some sample design sites we like;
- https://www.velmoreline.com/
- https://pindrask.io/
- https://www.glimbertic.com/live-chat-software/
- https://www.zavrolin.com/

Here are some competitor sites;
- https://www.ostrevaglinks.com/
- https://www.helpkestrel.com/

I have attached website content for your use.

Target Market(s)

eCommerce

Coding

Coded - Design and coding required

Number of Pages Required

5+ page

Font styles to use
Sans Serif

Colors

Designer to choose colors to be used in the design.

Requirements
Must have
• Must have designs for the following 5 separate pages;
• 1. Home (landing)
• - This will be were the design style really needs to show.
• - Just needs to touch on key services
• - CTA
• 2. About Us
• - Basic page for about me paragraph
• 3. Services
• - List of services with icons
• - Click on service type to expand details or hover over service icon to view popup bubble with details about that service
• 4. Pricing
• - Option to bundle 1(one) digital service plan and 1(one) call center service plan
• - Bundling adds 10% monthly discount to over all price
• - Customer does NOT have to bundle
• - FAQ
• 5. Contact Us
• - Include a capture form (name, company name, email, phone, message)
• - Contact info
• - Business hours
• When customer purchases their desired plan, then they are taken to a page where they must schedule a call with an account rep.
Nice to have
• home page animations
Should not have
• All information on Home/Landing page.

```html
<!DOCTYPE html>
<html lang="en">
<head>
<meta charset="utf-8">
<title>Lumora — Inbound and Outbound Calling & Marketing Services</title>
<link href="https://fonts.googleapis.com/css2?family=Roboto:wght@500;700;900&family=Poppins:wght@400;500;600&display=swap" rel="stylesheet">
<style>
:root{
  --green:#5bbb9c;
  --green-dark:#47a085;
  --ink:#1d2333;
  --text:#3a3f4a;
  --muted:#777c86;
  --grey-bg:#f4f4f4;
  --white:#ffffff;
  --hero-a:#5a5552;
  --hero-b:#2e2a28;
}
*{margin:0;padding:0;box-sizing:border-box}
html,body{width:1200px;height:3051px;overflow:hidden}
body{position:relative;background:var(--white);font-family:"Poppins",sans-serif;color:var(--text)}
.abs{position:absolute}

/* Hero */
.hero{left:0;top:0;width:1200px;height:690px}
.hero-photo{position:absolute;inset:0;background:linear-gradient(100deg,var(--hero-b) 0%,var(--hero-a) 45%,#8a6e5c 70%,#3b3533 100%)}
.hero-shade{position:absolute;inset:0;background:linear-gradient(90deg,rgba(0,0,0,.35),rgba(0,0,0,0) 60%)}
.nav{position:absolute;left:130px;top:40px;width:940px;height:64px;display:flex;align-items:center;justify-content:space-between}
.brand{display:flex;align-items:center;gap:16px;font-family:"Poppins",sans-serif;font-weight:500;font-size:31px;letter-spacing:6px;color:var(--white)}
.brand-dot{width:42px;height:42px;border-radius:50%;border:3px solid var(--green)}
.menu{display:flex;gap:30px;list-style:none;font-family:"Roboto",sans-serif;font-weight:500;font-size:15.5px;color:var(--white);letter-spacing:.3px}
.menu .active{color:var(--green)}
.hero-title{position:absolute;left:130px;top:236px;font-family:"Roboto",sans-serif;font-weight:900;font-size:38px;line-height:48px;color:var(--white);text-transform:uppercase}
.btn-ghost{position:absolute;left:130px;top:395px;width:167px;height:38px;border:2px solid var(--white);border-radius:20px;color:var(--white);font-family:"Roboto",sans-serif;font-weight:700;font-size:14px;display:flex;align-items:center;justify-content:center}
.dots{position:absolute;left:132px;top:469px;display:flex;gap:9px;align-items:center}
.dots span{width:8px;height:8px;border-radius:50%;background:var(--white)}
.dots .on{width:14px;height:14px;background:none;border:2px solid var(--white);position:relative}
.dots .on::after{content:"";position:absolute;inset:2px;border-radius:50%;background:var(--white)}
.divider{position:absolute;left:0;width:1200px}

/* Welcome */
.welcome-title{left:0;top:778px;width:1200px;text-align:center;font-family:"Roboto",sans-serif;font-weight:700;font-size:38px;color:var(--ink)}
.welcome-title em{font-style:normal;color:var(--green)}
.welcome-text{left:175px;top:844px;width:850px;text-align:center;font-size:13.4px;line-height:28.6px;color:var(--text)}
.btn-outline{left:541px;top:1015px;width:118px;height:36px;border:2px solid var(--ink);border-radius:18px;display:flex;align-items:center;justify-content:center;font-family:"Roboto",sans-serif;font-weight:700;font-size:14px;color:var(--ink)}

/* Services */
.services-bg{left:0;top:1130px;width:1200px;height:1010px}
.section-title{left:0;width:1200px;text-align:center;font-family:"Roboto",sans-serif;font-weight:700;font-size:38px;color:var(--ink);letter-spacing:.5px}
.tabs{left:378px;top:1379px;width:445px;height:38px;border:2px solid var(--green);border-radius:20px;display:flex;overflow:hidden;font-family:"Roboto",sans-serif;font-weight:500;font-size:19px}
.tabs span{flex:1;display:flex;align-items:center;justify-content:center;color:var(--ink)}
.tabs .active{background:var(--green);color:var(--white);border-radius:18px 0 0 18px}
.service{width:440px;height:130px}
.service .icon{position:absolute;left:0;top:0;width:118px;height:118px;border-radius:50%;background:var(--green);overflow:hidden}
.service .icon::before{content:"";position:absolute;left:50%;top:50%;width:140px;height:140px;background:var(--green-dark);transform:rotate(45deg);transform-origin:0 0}
.service .icon svg{position:absolute;left:29px;top:29px;width:60px;height:60px}
.service h3{position:absolute;left:142px;top:-8px;font-weight:500;font-size:18.5px;color:var(--ink)}
.service p{position:absolute;left:142px;top:24px;width:265px;font-size:11.6px;line-height:22.4px;color:var(--ink)}

/* Testimonials */
.testimonial{width:280px;height:220px}
.testimonial .quote{font-family:"Roboto",sans-serif;font-weight:900;font-size:40px;line-height:30px;height:26px;color:#b8bcc2}
.testimonial p{margin-top:4px;font-size:11.4px;line-height:21.5px;color:var(--muted)}
.person{position:absolute;left:0;top:120px;display:flex;gap:18px;align-items:center}
.avatar{width:76px;height:76px;border-radius:50%;border:3px solid #cfe6de;background:radial-gradient(circle at 50% 40%,#d8b79c,#8f9aa3)}
.person h4{font-weight:500;font-size:15px;line-height:20px;color:#2e6f8f}
.person small{display:block;font-size:11px;line-height:16px;color:var(--muted)}
.stars{margin-top:6px;display:flex;gap:5px}
.stars svg{width:13px;height:13px}

/* Footer */
.footer{left:0;top:2600px;width:1200px;height:358px}
.footer-band{position:absolute;left:0;top:40px;width:1200px;height:318px;background:var(--green)}
.footer h5{position:absolute;font-family:"Roboto",sans-serif;font-weight:500;font-size:18.5px;color:var(--white);letter-spacing:.3px}
.f-brand{position:absolute;left:120px;top:100px;width:190px;display:flex;flex-direction:column;align-items:center;gap:8px;font-weight:500;font-size:29px;letter-spacing:5px;color:var(--white)}
.f-brand .brand-dot{width:54px;height:54px;border-color:var(--white)}
.socials{position:absolute;left:157px;top:210px;display:flex;gap:5px}
.socials span{width:24px;height:24px;border-radius:50%;border:1.5px solid var(--white)}
.contact-list{position:absolute;left:338px;top:142px;list-style:none;font-size:12.2px;line-height:18px;color:var(--white)}
.contact-list li{position:relative;padding-left:32px;margin-bottom:12px}
.contact-list svg{position:absolute;left:2px;top:2px;width:14px;height:14px}
.news-text{position:absolute;left:620px;top:138px;width:290px;font-size:10.5px;line-height:19px;color:var(--white)}
.news-input{position:absolute;left:620px;top:196px;width:275px;height:38px;background:var(--white);font-size:10.5px;color:var(--ink);padding:12px 14px}
.news-btn{position:absolute;left:620px;top:250px;width:113px;height:34px;background:var(--ink);color:var(--white);font-family:"Roboto",sans-serif;font-weight:700;font-size:13.5px;display:flex;align-items:center;justify-content:center}
.quick{position:absolute;left:950px;top:138px;list-style:none;font-size:11.8px;line-height:22.4px;color:var(--white)}
.quick li::before{content:"›";margin-right:10px}
.copyright{left:0;top:2990px;width:1200px;text-align:center;font-size:12.2px;color:var(--ink)}
</style>
</head>
<body>

<header class="hero abs">
  <div class="hero-photo" role="img" aria-label="Photo of smiling call center agents wearing headsets at their desks"></div>
  <div class="hero-shade"></div>
  <nav class="nav">
    <div class="brand"><span class="brand-dot"></span>LUMORA</div>
    <ul class="menu">
      <li class="active">HOME</li><li>ABOUT US</li><li>SERVICES</li><li>PRICING</li><li>CONTACT US</li>
    </ul>
  </nav>
  <h1 class="hero-title">Inbound and<br>outbound calling &amp;<br>marketing services</h1>
  <div class="btn-ghost">GET MORE INFO</div>
  <div class="dots"><span class="on"></span><span></span><span></span><span></span></div>
  <svg class="divider" style="top:630px" width="1200" height="60" viewBox="0 0 1200 60" aria-hidden="true">
    <path d="M0,40 Q600,10 1200,40 L1200,60 L0,60 Z" fill="#fff"/>
    <circle cx="592" cy="40" r="17" fill="#1d2333"/>
  </svg>
</header>

<h2 class="welcome-title abs">WELCOME TO <em>LUMORA</em></h2>
<p class="welcome-text abs">Lumora is an omnichannel provider for customer care and back-end office support. We primarily work with eCommerce companies around the world. Our service is vital to the core operations and functionality of consumer-focused online eCommerce stores. Lumora originally started out as a generalized call center support company. Based in Oregon, the founder quickly realized that there was a lack of support for eCommerce owners that were just getting started. In 2018, Lumora switched gears to offer professional grade call center support at a price that even start-ups could afford.</p>
<div class="btn-outline abs">READ MORE</div>

<svg class="services-bg abs" viewBox="0 0 1200 1010" aria-hidden="true">
  <path d="M0,20 L620,50 C400,95 160,175 0,270 Z" fill="#5bbb9c"/>
  <path d="M0,300 C260,150 700,40 1200,15 L1200,880 Q600,1050 0,880 Z" fill="#f4f4f4"/>
</svg>

<h2 class="section-title abs" style="top:1298px">OUR SERVICES</h2>
<div class="tabs abs"><span class="active">Digital Services</span><span>Call Center Services</span></div>

<div class="service abs" style="left:152px;top:1500px">
  <div class="icon"><svg viewBox="0 0 60 60"><rect x="8" y="16" width="44" height="30" rx="3" fill="#fff"/><path d="M9 18 L30 34 L51 18" fill="none" stroke="#5bbb9c" stroke-width="3"/></svg></div>
  <h3>Email Support</h3>
  <p>Sed ut perspiciatis unde omnis iste natus error sit voluptatem accusantium doloremque laudantium, totam rem aperiam, eaque ipsa quae ab illo inventore</p>
</div>
<div class="service abs" style="left:642px;top:1500px">
  <div class="icon"><svg viewBox="0 0 60 60"><ellipse cx="30" cy="27" rx="22" ry="18" fill="#fff"/><path d="M16 38 L12 52 L28 43 Z" fill="#fff"/></svg></div>
  <h3>Live Chat Support</h3>
  <p>Sed ut perspiciatis unde omnis iste natus error sit voluptatem accusantium doloremque laudantium, totam rem aperiam, eaque ipsa quae ab illo inventore</p>
</div>
<div class="service abs" style="left:152px;top:1674px">
  <div class="icon"><svg viewBox="0 0 60 60"><circle cx="25" cy="25" r="14" fill="none" stroke="#fff" stroke-width="6"/><path d="M35 35 L50 50" stroke="#fff" stroke-width="8" stroke-linecap="round"/></svg></div>
  <h3>Product Research</h3>
  <p>Sed ut perspiciatis unde omnis iste natus error sit voluptatem accusantium doloremque laudantium, totam rem aperiam, eaque ipsa quae ab illo inventore</p>
</div>
<div class="service abs" style="left:642px;top:1674px">
  <div class="icon"><svg viewBox="0 0 60 60"><path d="M14 6 H36 L48 18 V54 H14 Z" fill="#fff"/><path d="M36 6 V18 H48" fill="#cfe9df"/><path d="M21 28 H41 M21 35 H41 M21 42 H41" stroke="#5bbb9c" stroke-width="3"/></svg></div>
  <h3>Product Listing</h3>
  <p>Sed ut perspiciatis unde omnis iste natus error sit voluptatem accusantium doloremque laudantium, totam rem aperiam, eaque ipsa quae ab illo inventore</p>
</div>
<div class="service abs" style="left:152px;top:1855px">
  <div class="icon"><svg viewBox="0 0 60 60"><path d="M8 14 L26 10 L52 36 L34 54 L8 28 Z" fill="#fff"/><circle cx="18" cy="20" r="4" fill="#5bbb9c"/><path d="M30 8 L56 34" stroke="#fff" stroke-width="3"/></svg></div>
  <h3>Price Monitoring</h3>
  <p>Sed ut perspiciatis unde omnis iste natus error sit voluptatem accusantium doloremque laudantium, totam rem aperiam, eaque ipsa quae ab illo inventore</p>
</div>
<div class="service abs" style="left:642px;top:1855px">
  <div class="icon"><svg viewBox="0 0 60 60"><rect x="6" y="14" width="48" height="32" rx="7" fill="#fff"/><path d="M25 22 L38 30 L25 38 Z" fill="#5bbb9c"/></svg></div>
  <h3>Product Photo &amp; Video Editing</h3>
  <p>Sed ut perspiciatis unde omnis iste natus error sit voluptatem accusantium doloremque laudantium, totam rem aperiam, eaque ipsa quae ab illo inventore</p>
</div>

<h2 class="section-title abs" style="top:2208px;font-size:33px;letter-spacing:1.5px">OUR CLIENTS SAYS</h2>

<div class="testimonial abs" style="left:137px;top:2300px">
  <div class="quote">“</div>
  <p>Lorem Ipsum is simply dummy text of the printing and typesetting industry. Lorem Ipsum has been the industry's standard dummy...</p>
  <div class="person"><div class="avatar" role="img" aria-label="Client portrait"></div><div><h4>Nadia L Brenner</h4><small>Lumora</small><div class="stars"><svg viewBox="0 0 10 10"><path d="M5 0 6.2 3.6 10 3.7 7 6 8.1 9.6 5 7.5 1.9 9.6 3 6 0 3.7 3.8 3.6Z" fill="#1d2333"/></svg><svg viewBox="0 0 10 10"><path d="M5 0 6.2 3.6 10 3.7 7 6 8.1 9.6 5 7.5 1.9 9.6 3 6 0 3.7 3.8 3.6Z" fill="#1d2333"/></svg><svg viewBox="0 0 10 10"><path d="M5 0 6.2 3.6 10 3.7 7 6 8.1 9.6 5 7.5 1.9 9.6 3 6 0 3.7 3.8 3.6Z" fill="#1d2333"/></svg><svg viewBox="0 0 10 10"><path d="M5 0 6.2 3.6 10 3.7 7 6 8.1 9.6 5 7.5 1.9 9.6 3 6 0 3.7 3.8 3.6Z" fill="#1d2333"/></svg><svg viewBox="0 0 10 10"><path d="M5 0 6.2 3.6 10 3.7 7 6 8.1 9.6 5 7.5 1.9 9.6 3 6 0 3.7 3.8 3.6Z" fill="#1d2333"/></svg></div></div></div>
</div>
<div class="testimonial abs" style="left:472px;top:2300px">
  <div class="quote">“</div>
  <p>Lorem Ipsum is simply dummy text of the printing and typesetting industry. Lorem Ipsum has been the industry's standard dummy...</p>
  <div class="person"><div class="avatar" role="img" aria-label="Client portrait"></div><div><h4>Nadia L Brenner</h4><small>Lumora</small><div class="stars"><svg viewBox="0 0 10 10"><path d="M5 0 6.2 3.6 10 3.7 7 6 8.1 9.6 5 7.5 1.9 9.6 3 6 0 3.7 3.8 3.6Z" fill="#1d2333"/></svg><svg viewBox="0 0 10 10"><path d="M5 0 6.2 3.6 10 3.7 7 6 8.1 9.6 5 7.5 1.9 9.6 3 6 0 3.7 3.8 3.6Z" fill="#1d2333"/></svg><svg viewBox="0 0 10 10"><path d="M5 0 6.2 3.6 10 3.7 7 6 8.1 9.6 5 7.5 1.9 9.6 3 6 0 3.7 3.8 3.6Z" fill="#1d2333"/></svg><svg viewBox="0 0 10 10"><path d="M5 0 6.2 3.6 10 3.7 7 6 8.1 9.6 5 7.5 1.9 9.6 3 6 0 3.7 3.8 3.6Z" fill="#1d2333"/></svg><svg viewBox="0 0 10 10"><path d="M5 0 6.2 3.6 10 3.7 7 6 8.1 9.6 5 7.5 1.9 9.6 3 6 0 3.7 3.8 3.6Z" fill="#1d2333"/></svg></div></div></div>
</div>
<div class="testimonial abs" style="left:806px;top:2300px">
  <div class="quote">“</div>
  <p>Lorem Ipsum is simply dummy text of the printing and typesetting industry. Lorem Ipsum has been the industry's standard dummy...</p>
  <div class="person"><div class="avatar" role="img" aria-label="Client portrait"></div><div><h4>Nadia L Brenner</h4><small>Lumora</small><div class="stars"><svg viewBox="0 0 10 10"><path d="M5 0 6.2 3.6 10 3.7 7 6 8.1 9.6 5 7.5 1.9 9.6 3 6 0 3.7 3.8 3.6Z" fill="#1d2333"/></svg><svg viewBox="0 0 10 10"><path d="M5 0 6.2 3.6 10 3.7 7 6 8.1 9.6 5 7.5 1.9 9.6 3 6 0 3.7 3.8 3.6Z" fill="#1d2333"/></svg><svg viewBox="0 0 10 10"><path d="M5 0 6.2 3.6 10 3.7 7 6 8.1 9.6 5 7.5 1.9 9.6 3 6 0 3.7 3.8 3.6Z" fill="#1d2333"/></svg><svg viewBox="0 0 10 10"><path d="M5 0 6.2 3.6 10 3.7 7 6 8.1 9.6 5 7.5 1.9 9.6 3 6 0 3.7 3.8 3.6Z" fill="#1d2333"/></svg><svg viewBox="0 0 10 10"><path d="M5 0 6.2 3.6 10 3.7 7 6 8.1 9.6 5 7.5 1.9 9.6 3 6 0 3.7 3.8 3.6Z" fill="#1d2333"/></svg></div></div></div>
</div>

<footer class="footer abs">
  <svg class="divider" style="top:0" width="1200" height="42" viewBox="0 0 1200 42" aria-hidden="true">
    <path d="M0,20 Q600,0 1200,20 L1200,42 L0,42 Z" fill="#5bbb9c"/>
  </svg>
  <div class="footer-band"></div>
  <div class="f-brand"><span class="brand-dot"></span>LUMORA</div>
  <div class="socials"><span></span><span></span><span></span><span></span></div>

  <h5 style="left:338px;top:92px">CONTACT US</h5>
  <ul class="contact-list">
    <li><svg viewBox="0 0 14 14"><path d="M7 1a4.5 4.5 0 0 0-4.5 4.5C2.5 9 7 13 7 13s4.5-4 4.5-7.5A4.5 4.5 0 0 0 7 1z" fill="#fff"/><circle cx="7" cy="5.5" r="1.6" fill="#5bbb9c"/></svg>Lumora<br>Harlow Creek, New York 3041-2270</li>
    <li><svg viewBox="0 0 14 14"><path d="M3 1h3l1 3-2 1.5a8 8 0 0 0 3.5 3.5L10 7l3 1v3a2 2 0 0 1-2 2A11 11 0 0 1 1 3a2 2 0 0 1 2-2z" fill="#fff"/></svg><span style="font-size:13.5px">Phone: (555) 214-7730</span></li>
    <li><svg viewBox="0 0 14 14"><rect x="1" y="3" width="12" height="8" fill="#fff"/><path d="M1.5 3.5 7 8l5.5-4.5" fill="none" stroke="#5bbb9c" stroke-width="1.2"/></svg>Email: info@lumora.com</li>
  </ul>

  <h5 style="left:620px;top:92px">SIGN UP FOR NEWSLETTER</h5>
  <p class="news-text">Excepteur sint occaecat cupidatat non proident, sunt in culpa qui officia deserunt</p>
  <div class="news-input">Enter email</div>
  <div class="news-btn">SIGN UP</div>

  <h5 style="left:946px;top:92px">QUICK LINKS</h5>
  <ul class="quick"><li>Home</li><li>About Us</li><li>Services</li><li>Pricing</li><li>Blog</li><li>Contact Us</li></ul>
</footer>

<p class="copyright abs">© Copyright 2018 Lumora. All Rights Reserved.</p>

</body>
</html>
```